Logo and Card design for KRV Home Solutions LLC

I need an edgier logo and business card designs. Current logo attached. I like the colors below. I would like the logo to incorporate a home in the design.
Title = Principal-Acquisitions
Email:KRVHOMESOLUTIONS@fernmail.example
555-214-0937
facebook
IG
2 sided business card with the front being contact info a slogan about selling a home fast. The back incorporating What we do. Buy houses, land, or commercial property as is. We find solutions to make the process of selling simple and fair.

Target Market(s)

Motivated house sellers.

Industry/Entity Type

Business

Contact Information for Business Card

Who we are: We are a Faith based Real Estate Investment Company. We pay cash for homes in any condition and can close quick. Whatever the reason you need to sell fast, we can help. We believe in creating win-win solutions to help you in your time of need. We care! We can help!

Logo Text

KRV Home Solutions LLC

Font styles to use
Sans Serif

Colors
33a6d7
0355a3
85abd2
cee9f5
9d9d9d
b2b2b2
ffffff

Requirements
Must have
• Old logo attached. I want something edgier.
• Company name, phone number, description on the back of what we can do. Pay all cash. Buy in as is condition. No fees,Commisions or closing costs.Close quick. No hassles with solutions to meet your unique situation.
• Call today for an offer within 24 hours.

```html
<!DOCTYPE html>
<html lang="en">
<head>
<meta charset="utf-8">
<title>KRV Home Solutions – Business Card</title>
<link rel="stylesheet" href="https://fonts.googleapis.com/css2?family=Lato:wght@400;700&display=swap">
<style>
  :root {
    --stage: #b1b4bc;
    --navy: #1f3a72;
    --navy-deep: #1b3368;
    --blue: #1d4b9a;
    --grey: #7a7d85;
    --ink: #2e2e33;
    --white: #ffffff;
    --paper: #f7f8fb;
  }
  * { box-sizing: border-box; margin: 0; padding: 0; }
  html, body { width: 1200px; height: 900px; overflow: hidden; }
  body {
    background: var(--stage);
    font-family: "Lato", Arial, sans-serif;
    position: relative;
  }
  .card {
    position: absolute;
    top: 306px;
    width: 440px;
    height: 272px;
    box-shadow: 3px 3px 5px rgba(0,0,0,.45);
    overflow: hidden;
  }
  .card--front { left: 149px; background: var(--white); }
  .card--back { left: 608px; background: var(--navy); }

  .accent-bars { position: absolute; left: 0; top: 26px; }
  .person { position: absolute; left: 35px; top: 31px; }
  .person__name { color: var(--blue); font-size: 16.5px; font-weight: 700; letter-spacing: .2px; }
  .person__title { color: var(--ink); font-size: 13px; margin-top: 1px; }

  .company-name {
    position: absolute; left: 236px; top: 84px; width: 180px;
    color: var(--navy); font-size: 22px; font-weight: 700;
    text-align: center; line-height: 1.2;
  }

  .contact { position: absolute; left: 31px; top: 177px; color: var(--ink); }
  .contact__row { display: flex; align-items: center; gap: 5px; }
  .contact__row--phone { font-size: 15px; }
  .contact__row--mail { font-size: 13px; margin-top: 2px; }

  .social { position: absolute; left: 360px; top: 183px; display: flex; gap: 6px; }
  .social__dot { width: 23px; height: 23px; border-radius: 50%; background: var(--navy); }

  .cta-band {
    position: absolute; left: 0; bottom: 0; width: 100%; height: 46px;
    display: flex; align-items: center; justify-content: center;
    font-size: 13px; font-weight: 700; letter-spacing: .1px;
  }
  .card--front .cta-band { background: var(--navy); color: var(--white); }
  .card--back .cta-band { background: var(--paper); color: var(--navy-deep); }

  .back-glow {
    position: absolute; inset: 0 0 46px 0;
    background: linear-gradient(135deg, #2a4783 0%, #1f3a72 45%, #223e78 100%);
  }
  .back-name {
    position: absolute; left: 0; top: 88px; width: 100%;
    color: var(--white); font-size: 32px; font-weight: 700;
    text-align: center; line-height: 1;
  }
  .back-rule {
    position: absolute; left: 18px; right: 17px; top: 162px;
    height: 1px; background: rgba(255,255,255,.75);
  }
  .services {
    position: absolute; left: 0; top: 170px; width: 100%;
    color: var(--white); font-size: 11.6px; text-align: center; line-height: 14px;
  }
</style>
</head>
<body>

<section class="card card--front">
  <svg class="accent-bars" width="30" height="38" viewBox="0 0 30 38" aria-hidden="true">
    <polygon points="0,0 12,0 16,37 0,37" fill="#7a7d85"/>
    <polygon points="14,0 28,0 28,37 18,37" fill="#1f3a72"/>
  </svg>
  <div class="person">
    <div class="person__name">MARCUS ELLERY</div>
    <div class="person__title">Principal-Acquisitions</div>
  </div>

  <div class="company-name">KRV Home Solutions LLC</div>

  <div class="contact">
    <div class="contact__row contact__row--phone">
      <svg width="11" height="10" viewBox="0 0 12 10" aria-hidden="true">
        <path d="M1 3c0-2 10-2 10 0v1H8.5V2.8h-5V4H1z M3 4.5h6l1.5 4.5h-9z" fill="#2e2e33"/>
      </svg>
      <span>555-214-0937</span>
    </div>
    <div class="contact__row contact__row--mail">
      <svg width="10" height="8" viewBox="0 0 10 8" aria-hidden="true">
        <rect width="10" height="8" fill="#2e2e33"/>
        <path d="M0.5 0.8 5 4.5 9.5 0.8" stroke="#fff" stroke-width="1" fill="none"/>
      </svg>
      <span>KRVHOMESOLUTIONS@fernmail.example</span>
    </div>
  </div>

  <div class="social" aria-label="Social profiles">
    <span class="social__dot"></span>
    <span class="social__dot"></span>
  </div>

  <div class="cta-band">CALL TODAY TO GET AN ALL CASH OFFER WITHIN 24 HOURS</div>
</section>

<section class="card card--back">
  <div class="back-glow"></div>
  <div class="back-name">KRV Home Solutions LLC</div>
  <div class="back-rule"></div>
  <p class="services">
    Buy houses, land or commercial property as is | Pay all cash | Buy in as is condition<br>
    No fees, commisions or closing costs. | Close quick.<br>
    No hassles with solutions to meet your unique situation
  </p>
  <div class="cta-band">CALL TODAY TO GET AN ALL CASH OFFER WITHIN 24 HOURS</div>
</section>

</body>
</html>
```